Local Flower Farm Needs Business Card Design

I need business cards designed for a flower farm based in Eudora, Kansas.
Business Info:
We are a local cut flower farm located in Eudora, Kansas, founded by Corinne Haldwick. What started as a passion for agriculture and search for more joy in daily life has blossomed into a small business dedicated to providing the community with beautiful, fresh, and sustainable flowers. We specialize in local, seasonal blooms, ensuring that every petal reflects the care and dedication we pour into our craft. Our mission is to deliver the highest quality flowers directly to our customers through local farmers markets and to florists who share our commitment to sustainability. Join us in celebrating the beauty of nature, one bloom at a time!
Contact Details:
Corinne Haldwick
Owner
Phone 913-555-0147
Facebook: Rosalind Thorpe Gardens
Instagram: @RosalindThorpeGardens
Website: RosalindThorpeGardens.example
Target Market(s)
Wholesale to Florists and Direct to Consumer via Farmers Market
Industry/Entity Type
Florist, Farm
Contact Information for Business Card
Name, Contact Info, Logo
Look and feel
Each slider illustrates characteristics of the customer's brand and the style your logo design should communicate.

```html
<!DOCTYPE html>
<html lang="en">
<head>
<meta charset="utf-8">
<title>Rosalind Thorpe Gardens – Business Card</title>
<link rel="stylesheet" href="https://fonts.googleapis.com/css2?family=Cinzel:wght@500&family=Outfit:wght@400&display=swap">
<style>
  :root {
    --teal: #0d2f35;
    --teal-line: #2c8a96;
    --paper: #f3f3f1;
    --ink: #12343a;
    --text: #1a1a1a;
    --silver: #b9c5c8;
    --stage: #1c1c1d;
    --divider: #dcdcda;
  }
  * { box-sizing: border-box; margin: 0; padding: 0; }
  html, body { width: 1200px; height: 900px; overflow: hidden; background: var(--stage); }
  .canvas { position: relative; width: 1200px; height: 900px; }

  .card {
    position: absolute; left: 320px; width: 560px; height: 320px;
    border-radius: 26px; overflow: hidden;
  }
  .card--front { top: 80px; background: var(--paper); }
  .card--back  { top: 500px; background: var(--teal); }

  .card__wave { position: absolute; inset: 0; width: 560px; height: 320px; }

  .brand-seal {
    position: absolute; width: 190px; height: 190px; border-radius: 50%;
    display: flex; align-items: center; justify-content: center; text-align: center;
    font-family: "Cinzel", serif; font-weight: 500; letter-spacing: 2px;
  }
  .card--front .brand-seal {
    left: 28px; top: 56px; border: 1.2px solid var(--ink); color: var(--ink);
    font-size: 17px; line-height: 1.35;
  }
  .card--back .brand-seal {
    left: 180px; top: 55px; width: 200px; height: 200px;
    border: 1.2px solid var(--silver); color: var(--silver);
    font-size: 18px; line-height: 1.35;
  }

  .divider {
    position: absolute; left: 238px; top: 28px; width: 1px; height: 215px;
    background: var(--divider);
  }

  .contact { position: absolute; left: 262px; top: 40px; color: var(--ink); }
  .contact__name {
    font-family: "Cinzel", serif; font-weight: 500; font-size: 21px; letter-spacing: 1px;
    line-height: 1.3;
  }
  .contact__role { font-family: "Outfit", sans-serif; font-size: 13px; line-height: 1.3; }
  .contact__list { list-style: none; margin-top: 12px; }
  .contact__item {
    display: flex; align-items: center; gap: 8px; height: 24px;
    font-family: "Outfit", sans-serif; font-size: 14.5px; color: var(--text);
  }
  .contact__icon {
    width: 18px; height: 18px; border: 1px solid #333; border-radius: 50%;
    display: flex; align-items: center; justify-content: center; flex: none;
  }
  .contact__icon svg { width: 10px; height: 10px; }
</style>
</head>
<body>
<main class="canvas">

  <section class="card card--front">
    <svg class="card__wave" viewBox="0 0 560 320" aria-hidden="true">
      <path d="M0,264 C150,278 300,254 400,230 C470,214 520,208 560,206" fill="none" stroke="var(--teal)" stroke-width="1.5"/>
      <path d="M0,278 C150,292 300,268 400,244 C470,228 520,222 560,220 L560,320 L0,320 Z" fill="var(--teal)"/>
      <path d="M0,287 C150,299 300,276 400,252 C470,236 520,231 560,229" fill="none" stroke="var(--teal-line)" stroke-width="0.8"/>
    </svg>

    <div class="brand-seal">Rosalind<br>Thorpe<br>Gardens</div>
    <div class="divider"></div>

    <div class="contact">
      <h1 class="contact__name">CORINNE HALDWICK</h1>
      <p class="contact__role">Owner</p>
      <ul class="contact__list">
        <li class="contact__item">
          <span class="contact__icon"><svg viewBox="0 0 10 10"><path d="M2,1 L4,1 L4.6,3 L3.5,3.8 C4,5 5,6 6.2,6.5 L7,5.4 L9,6 L9,8 C9,8.6 8.5,9 8,9 C4.5,8.8 1.2,5.5 1,2 C1,1.5 1.4,1 2,1 Z" fill="#222"/></svg></span>
          913-555-0147
        </li>
        <li class="contact__item">
          <span class="contact__icon"><svg viewBox="0 0 10 10"><path d="M1.5,2 H8.5 V6.5 H4.5 L2.5,8.5 V6.5 H1.5 Z" fill="#222"/></svg></span>
          Rosalind Thorpe Gardens
        </li>
        <li class="contact__item">
          <span class="contact__icon"><svg viewBox="0 0 10 10"><path d="M5,8.8 L1.6,5.3 C0.6,4.2 0.9,2.3 2.4,1.9 C3.4,1.6 4.3,2.1 5,3 C5.7,2.1 6.6,1.6 7.6,1.9 C9.1,2.3 9.4,4.2 8.4,5.3 Z" fill="#222"/></svg></span>
          @RosalindThorpeGardens
        </li>
        <li class="contact__item">
          <span class="contact__icon"><svg viewBox="0 0 10 10" fill="none" stroke="#222" stroke-width="0.9"><circle cx="5" cy="5" r="4"/><ellipse cx="5" cy="5" rx="1.8" ry="4"/><line x1="1" y1="5" x2="9" y2="5"/></svg></span>
          RosalindThorpeGardens.example
        </li>
      </ul>
    </div>
  </section>

  <section class="card card--back">
    <div class="brand-seal">Rosalind<br>Thorpe<br>Gardens</div>
  </section>

</main>
</body>
</html>
```